Need Help having my business card stand out

I am the owner of Birchway Canine Training and would like for my business cards to stand out. I have been trying to keep designing them myself but I can't get what I have in my head on the card. I will try my best to post templates that I like for inspirations. I want something unique but elegant. I don't want in to look cartoony or cheesy. It needs to pop in a pet shop but also in a coffee shop or gym.

Target Market(s)

Dog owners, Married ,No young kids Jr High school kids and up (maybe kids on the way) Executives, Stay at home moms/wives, Small business owners

Industry/Entity Type

Dog Training

Contact Information for Business Card

Lowell Spratt, 281-904-3376, info@birchwaycanine.example, www.birchwaycanine.example

Colors

Designer to choose colors to be used in the design.

Requirements
Must have
• my logo
Should not have
• Cursive lettering

```html
<!DOCTYPE html>
<html lang="en">
<head>
<meta charset="utf-8">
<title>Birchway Canine Training – Business Card</title>
<link rel="stylesheet" href="https://fonts.googleapis.com/css2?family=Open+Sans:wght@400;600&display=swap">
<style>
  :root {
    --backdrop: #e7e4df;
    --card-white: #f2f1ee;
    --navy: #1c1d2f;
    --ink: #111111;
    --text: #1a1a1a;
    --photo-light: #d9d6cc;
    --photo-mid: #7c6a5a;
    --photo-dark: #3c4a2e;
  }
  * { box-sizing: border-box; margin: 0; padding: 0; }
  html, body {
    width: 1200px; height: 900px; overflow: hidden;
    background: var(--backdrop);
    font-family: "Open Sans", Arial, sans-serif;
  }
  .canvas {
    position: relative; width: 1200px; height: 900px;
  }
  .card {
    position: absolute; left: 320px;
    width: 560px; height: 320px;
    overflow: hidden;
    box-shadow: 0 6px 18px rgba(0,0,0,0.18);
  }
  /* Back side */
  .card--back { top: 110px; display: flex; }
  .card-back__photo {
    width: 46%; height: 100%;
    background: linear-gradient(160deg, var(--photo-light) 0%, var(--photo-mid) 55%, var(--photo-dark) 100%);
  }
  .card-back__brand {
    flex: 1; background: var(--navy);
    display: flex; align-items: center; justify-content: center;
    padding: 0 30px;
  }
  .brand-name {
    font-weight: 600; text-align: center; line-height: 1.15;
    letter-spacing: 0.04em; text-transform: uppercase;
  }
  .card-back__brand .brand-name { color: var(--card-white); font-size: 26px; }

  /* Front side */
  .card--front { top: 470px; background: var(--card-white); }
  .card-front__brand {
    position: absolute; right: 34px; top: 40px; width: 210px;
    color: var(--ink); font-size: 22px;
  }
  .card-front__name {
    position: absolute; left: 40px; top: 112px;
    font-size: 24px; font-weight: 600; letter-spacing: 0.01em;
    color: var(--text); text-transform: uppercase;
  }
  .contact-list {
    position: absolute; left: 40px; top: 170px;
    list-style: none;
  }
  .contact-list li {
    display: flex; align-items: center; gap: 10px;
    font-size: 17px; color: var(--text); line-height: 26px;
  }
  .contact-list svg { width: 15px; height: 15px; fill: var(--text); flex: none; }
  .card-front__band {
    position: absolute; left: 0; right: 0; bottom: 0; height: 56px;
    background: var(--ink);
  }
</style>
</head>
<body>
<main class="canvas">
  <section class="card card--back">
    <div class="card-back__photo" role="img" aria-label="Photo of the trainer kneeling outdoors on grass beside his dog"></div>
    <div class="card-back__brand">
      <p class="brand-name">Birchway Canine Training</p>
    </div>
  </section>

  <section class="card card--front">
    <p class="brand-name card-front__brand">Birchway Canine Training</p>
    <h1 class="card-front__name">Lowell Spratt</h1>
    <ul class="contact-list">
      <li>
        <svg viewBox="0 0 24 24" aria-hidden="true"><path d="M6.6 10.8a15.1 15.1 0 0 0 6.6 6.6l2.2-2.2a1 1 0 0 1 1-.25 11.4 11.4 0 0 0 3.6.57 1 1 0 0 1 1 1V20a1 1 0 0 1-1 1A17 17 0 0 1 3 4a1 1 0 0 1 1-1h3.5a1 1 0 0 1 1 1c0 1.25.2 2.45.57 3.57a1 1 0 0 1-.25 1z"/></svg>
        281-904-3376
      </li>
      <li>
        <svg viewBox="0 0 24 24" aria-hidden="true"><path d="M2 5h20v14H2z M4 7v.4l8 5.2 8-5.2V7z" fill-rule="evenodd"/></svg>
        info@birchwaycanine.example
      </li>
      <li>
        <svg viewBox="0 0 24 24" aria-hidden="true"><path d="M12 2a10 10 0 1 0 0 20 10 10 0 0 0 0-20zm-1 17.9A8 8 0 0 1 4.1 11H8v2l3 3zm6.9-2.5A2 2 0 0 0 16 16h-1v-3H9v-2h2V9h2V6.5A8 8 0 0 1 17.9 17.4z"/></svg>
        www.birchwaycanine.example
      </li>
    </ul>
    <div class="card-front__band"></div>
  </section>
</main>
</body>
</html>
```